TLK Electricial Contracting Services

Hi guys, after a design for my small electrical company, have logo design files to be incorporated into the layout, the basic concept is electrical contracting services for residential, commercial, industrial & data services, image is clean clear and strong,

Card format is to have a nice clean logo on front,with maybe the Residential – commercial – industrial - data, followed with licensed & insured, followed by contact details on backside of the card.

Target Market(s)

Residential, commercial, industrial sectors.

Industry/Entity Type

Electrical

Contact Information for Business Card

TLK logo,
Residential – commercial – industrial - data
REC: 61307
Email: tlk@vornamail.net.au
Phone: 0487 352 019

Requirements
Must have
• Clean & strong design.
Nice to have
• If possible, I would like the logo colours inverted so the text is orange and the background is black on the front of the card, then the backside of the card be the reverse colour
Should not have
• No Sparks, lightning bolts,

```html
<!DOCTYPE html>
<html lang="en">
<head>
<meta charset="utf-8">
<title>TLK Electrical – Business Card</title>
<link rel="stylesheet" href="https://fonts.googleapis.com/css2?family=Play:wght@400;700&display=swap">
<style>
  :root {
    --backdrop: #2d2a28;
    --card-black: #141414;
    --orange: #ee7a16;
    --white: #f4f4f4;
    --ink: #121212;
    --rule: #4a4a4a;
  }
  * { box-sizing: border-box; margin: 0; padding: 0; }
  html, body {
    width: 1200px; height: 716px; overflow: hidden;
    background: var(--backdrop);
    font-family: "Play", sans-serif;
  }
  .stage { position: relative; width: 1200px; height: 716px; }

  .card {
    position: absolute; top: 208px;
    width: 530px; height: 300px;
    border-radius: 10px; overflow: hidden;
    background: var(--card-black);
    box-shadow: 0 10px 24px rgba(0,0,0,.45);
  }

  /* Front */
  .card-front { left: 45px; }
  .front-brand { position: absolute; left: 52px; top: 34px; }
  .front-mark {
    display: block; color: var(--orange);
    font-weight: 700; font-size: 118px; line-height: 1; letter-spacing: 2px;
  }
  .front-name {
    display: block; color: var(--orange);
    font-weight: 700; font-size: 27px; line-height: 1.1; margin-top: 2px;
  }
  .front-sectors {
    display: block; color: var(--white);
    font-size: 15px; margin-top: 8px; padding-top: 6px;
    border-top: 1px solid var(--rule); letter-spacing: .3px;
  }
  .front-phone {
    position: absolute; right: 14px; top: 50%;
    transform: translateY(-50%) rotate(90deg);
    transform-origin: center;
    color: var(--white); font-weight: 700; font-size: 22px;
    letter-spacing: 1px; white-space: nowrap;
    width: 40px; display: flex; justify-content: center;
  }

  /* Back */
  .card-back { left: 625px; }
  .back-tab {
    position: absolute; left: 14px; top: 40px;
    width: 8px; height: 70px; border-radius: 4px;
    background: var(--orange);
  }
  .back-brand {
    position: absolute; left: 40px; top: 28px; height: 244px;
    writing-mode: vertical-rl; transform: rotate(180deg);
    display: flex; flex-direction: column;
  }
  .back-mark {
    color: var(--white); font-weight: 700;
    font-size: 70px; line-height: 1; letter-spacing: 2px;
  }
  .back-name {
    color: var(--white); font-weight: 700; font-size: 14px;
    margin-left: 4px; padding-left: 4px; border-left: 1px solid var(--rule);
  }
  .back-sectors {
    color: var(--orange); font-weight: 700; font-size: 15px; line-height: 1.3;
    margin-left: 6px;
  }
  .back-panel {
    position: absolute; left: 225px; top: 0; right: 0; bottom: 0;
    background: var(--orange);
    border-top-left-radius: 10px;
    padding: 40px 24px 0 28px; color: var(--ink);
  }
  .reg { font-weight: 700; font-size: 17px; margin-bottom: 14px; }
  .services { list-style: none; font-weight: 700; font-size: 16px; line-height: 1.2; }
  .contact { margin-top: 16px; list-style: none; }
  .contact li { display: flex; align-items: center; gap: 8px; }
  .contact-email { font-size: 14px; }
  .contact-phone { font-weight: 700; font-size: 18px; }
  .contact svg { width: 12px; height: 12px; flex: none; }
</style>
</head>
<body>
<main class="stage">

  <section class="card card-front" aria-label="Card front">
    <div class="front-brand">
      <span class="front-mark">TLK</span>
      <span class="front-name">Tasman Lee Kirby Electrical</span>
      <span class="front-sectors">Residential – Commercial – Industrial – Data</span>
    </div>
    <div class="front-phone">0487 352 019</div>
  </section>

  <section class="card card-back" aria-label="Card back">
    <span class="back-tab"></span>
    <div class="back-brand">
      <span class="back-mark">TLK</span>
      <span class="back-name">Tasman Lee Kirby Electrical</span>
      <span class="back-sectors">Residential – Commercial<br>Industrial – Data</span>
    </div>
    <div class="back-panel">
      <p class="reg">REC: 61307</p>
      <ul class="services">
        <li>New installations Additions</li>
        <li>Rewiring Repairs</li>
        <li>Maintenance 24 hours</li>
        <li>Faults and Emergency</li>
        <li>Assistance</li>
      </ul>
      <ul class="contact">
        <li class="contact-email">
          <svg viewBox="0 0 12 12" aria-hidden="true"><rect x="1" y="2.5" width="10" height="7" fill="none" stroke="#121212" stroke-width="1.2"/><path d="M1 3l5 4 5-4" fill="none" stroke="#121212" stroke-width="1.2"/></svg>
          tlk@vornamail.net.au
        </li>
        <li class="contact-phone">
          <svg viewBox="0 0 12 12" aria-hidden="true"><rect x="3" y="1" width="6" height="10" rx="1.2" fill="#121212"/><rect x="4" y="2.2" width="4" height="6" fill="#ee7a16"/></svg>
          0487 352 019
        </li>
      </ul>
    </div>
  </section>

</main>
</body>
</html>
```